Employment Agency Website Design

We are working with an employment agency in California.

Some sites to use for content/competitors and inspiration:

https://www.pinecrestjobs.com/us/en
https://www.velmorusa.com
https://www.dravenworks.us
https://www.quillora.com/en
https://www.tomvalusa.com
https://www.fernstaffing.com

Thank you for taking the time to consider designing a website for us. We are web developers based in Stockton, CA, USA. Most of our projects go through the same process. Understanding this process may help you win a project with us. We custom-code all of our websites in-house. We don’t have any requirements as to what tools you use for your design, but we prefer Figma files. For any design that we label as four-stars, we send it to the client for review. The client picks the final design they want us to use. Once we complete this process, we will continue to show additional clients all the four-star sites and purchase them later. Your designs will have multiple chances to sell. For better chances of success, we ask that you follow these guidelines.

IMAGES:
If you use any images or icons in the design, we ask that you have a link to the asset so we can purchase the image/icon. Most of the designs we submit do not have the customer’s images on them unless they have some great images. Be creative; show us the feeling you are trying to portray with your image choices. Use any royalty-free site you choose. We subscribe to Adobe and mainly use their images, but we can purchase images outside of Adobe. PLEASE NOTE: we will not submit designs to clients with watermarks on the images.

FONTS:
We ask that you identify the fonts used in the design. This can be done in a message if you want. We typically use Google Fonts and Adobe Fonts.

CONTENT:
We're always open to different content and ideas. We often submit designs with stock images so the client can see our vision. We typically take pictures after the website launch to use their images with our vision. Lorem Ipsum is fine for paragraphs, but we ask that you write the headers in correct English. We want to be able to show the vision and identify the sections of the website.

INSPIRATION:
We typically add a couple of links in the brief of websites we like to help you get started in your design.

REVISIONS:
We do not often ask for revisions of the designs unless we see something in the design that may not appeal to the client. If there are slight changes that we want to make, we do that in the development process.

FEEDBACK:
We rarely give feedback on designs during the design process. We are working on many website projects and do not have the time to provide feedback. We usually respond if your request is well thought out and asks specific questions, but a note asking “feedback, please” usually goes unanswered.

```html
<!DOCTYPE html>
<html lang="en">
<head>
<meta charset="utf-8">
<title>Norvale Talent – Find Your Dream Job</title>
<link href="https://fonts.googleapis.com/css2?family=Poppins:ital,wght@0,300;0,400;0,500;0,600;0,700;1,600&display=swap" rel="stylesheet">
<style>
:root{
  --red:#c8202f;
  --red-dark:#a81825;
  --red-soft:#e9a3aa;
  --track:#f3c9cd;
  --blush:#fdf1f2;
  --ink:#1d1d1f;
  --muted:#555a60;
  --white:#ffffff;
  --footer:#0c0c0e;
}
*{box-sizing:border-box;margin:0;padding:0}
html,body{width:1200px;height:4831px;overflow:hidden}
body{font-family:'Poppins',sans-serif;color:var(--ink);background:var(--white);position:relative}
.wrap{width:976px;margin:0 auto;position:relative}
section{position:relative;overflow:hidden}
.section-title{font-size:42px;font-weight:600;color:var(--red);text-align:center}
p{font-size:14px;line-height:26px;color:var(--muted)}

/* header */
.site-header{height:84px;display:flex;align-items:center;padding:0 112px;justify-content:space-between}
.brand{display:flex;align-items:center;gap:8px}
.brand-mark{width:22px;height:22px;background:var(--red);border-radius:50%}
.brand-name{font-size:22px;font-weight:600;color:var(--red)}
.main-nav{display:flex;gap:22px;font-size:13px;margin-left:60px}
.main-nav span::after{content:" ⌄";font-size:12px}
.header-tools{display:flex;align-items:center;gap:22px;font-size:13px}

/* hero */
.hero{height:653px;background:linear-gradient(100deg,#2a2420 0%,#3f3a35 45%,#6b6155 70%,#3b3733 100%);color:var(--white)}
.hero-photo{position:absolute;inset:0}
.hero-content{position:absolute;left:112px;top:155px;width:560px}
.hero h1{font-size:40px;font-weight:600;line-height:56px}
.hero p{color:#f1f1f1;font-size:14px;line-height:23px;margin-top:14px}
.search-box{position:absolute;left:112px;top:385px;width:675px;height:127px;background:var(--red);border-radius:18px;padding:22px 38px}
.search-labels{display:flex;font-size:17px;font-weight:500}
.search-labels div{width:276px;display:flex;align-items:center;gap:10px}
.search-fields{display:flex;gap:28px;margin-top:14px;align-items:center}
.field{width:250px;height:36px;border:1px solid #f1c3c7;border-radius:2px;font-size:13px;padding:8px 14px;color:#f7dadd}
.search-btn{width:46px;height:34px;background:#0d0d0d;border-radius:4px;display:flex;align-items:center;justify-content:center}

/* categories */
.categories{height:562px;padding-top:75px}
.cat-row{display:flex;gap:25px;margin-top:54px}
.cat-card{width:225px;height:237px;border:1px solid #bfbfbf;border-radius:22px;box-shadow:0 5px 0 #d9d9d9;text-align:center;padding-top:22px}
.cat-card h3{font-size:20px;font-weight:500;margin-top:10px}
.cat-card small{font-size:14px;color:#333}
.dots{display:flex;gap:12px;justify-content:center}
.dots i{width:18px;height:18px;border-radius:50%;background:var(--red-soft)}
.dots i.on{background:var(--red)}

/* about */
.about{height:529px;background:var(--blush)}
.about-text{position:absolute;left:112px;top:75px;width:550px}
.about h2{font-size:40px;font-weight:600;color:var(--red)}
.about h4{font-size:20px;font-weight:600;margin:30px 0 12px}
.about p{text-align:justify}
.ticks{list-style:none;margin-top:18px}
.ticks li{font-size:16px;display:flex;align-items:center;gap:10px;margin-bottom:12px}
.ticks li::before{content:"✓";width:18px;height:18px;border-radius:50%;background:var(--red);color:#fff;font-size:11px;display:flex;align-items:center;justify-content:center}
.about-photo{position:absolute;left:714px;top:86px;width:375px;height:357px;border-radius:28px;background:linear-gradient(135deg,#3c4347,#9a9b98 50%,#d7d3cc)}

/* how */
.how{height:516px;padding-top:72px}
.steps{display:flex;justify-content:space-between;margin-top:40px;padding:0 20px}
.step{width:260px;text-align:center}
.step .num{display:inline-block;color:var(--red);font-size:20px;font-weight:500;border-bottom:2px solid var(--red);line-height:24px;margin-top:22px}
.step h3{font-size:20px;font-weight:500;margin-top:10px}
.step p{line-height:24px;margin-top:4px}
.arrow{position:absolute}

/* cv band */
.cv-band{height:352px;background:linear-gradient(90deg,#fdeeee,#f7e7e6 50%,#fbeeee)}
.cv-photo{position:absolute;left:110px;top:18px;width:360px;height:334px;border-radius:180px 180px 0 0;background:linear-gradient(180deg,#f6d9d9,#c9cad6)}
.cv-text{position:absolute;left:538px;top:118px;width:560px}
.cv-text h3{font-size:19px;font-weight:600}
.cv-text p{line-height:26px;margin-top:8px}
.btn{display:inline-flex;align-items:center;gap:8px;background:var(--red);color:#fff;font-size:14px;padding:6px 20px;border-radius:3px;margin-top:12px}

/* testimonials */
.testimonials{height:628px;padding-top:90px}
.quotes{display:flex;justify-content:space-between;margin-top:50px;padding:0 10px}
.quote{width:270px;text-align:center}
.quote p{letter-spacing:1.2px;line-height:26px;margin-top:18px}
.quote h4{font-style:italic;font-weight:600;font-size:20px;letter-spacing:2px;margin-top:14px}

/* opportunities */
.opps{height:495px;background:linear-gradient(180deg,#fdf3f3,#f8ebec)}
.opps-text{position:absolute;left:112px;top:95px;width:550px}
.opps h2{font-size:42px;font-weight:600;color:var(--red);line-height:55px}
.opps p{text-align:justify;margin-top:30px}
.opps .btn{width:185px;justify-content:center;margin-top:16px}
.features{position:absolute;left:718px;top:80px;width:400px}
.feature{display:flex;gap:22px;margin-bottom:32px}
.feature-icon{width:68px;height:68px;background:var(--red);border-radius:10px;flex:none;display:flex;align-items:center;justify-content:center}
.feature h4{font-size:20px;font-weight:500}
.feature p{line-height:26px;margin-top:4px}

/* insights */
.insights{height:714px;padding-top:75px}
.post-row{display:flex;gap:19px;position:absolute;left:-58px;top:168px}
.post{width:315px;flex:none}
.post-img{height:204px;border-radius:12px}
.post h4{font-size:19px;font-weight:500;color:var(--red);text-decoration:underline;margin-top:22px;line-height:26px;white-space:nowrap}
.post p{text-align:justify;line-height:23px;margin-top:8px}
.progress{position:absolute;left:112px;top:549px;width:976px;height:5px;background:var(--track)}
.progress i{position:absolute;left:195px;top:0;width:313px;height:5px;background:var(--red)}
.pager{position:absolute;left:528px;top:588px;display:flex;gap:44px}
.pager span{width:50px;height:42px;border:2px solid var(--red);border-radius:3px;display:flex;align-items:center;justify-content:center;font-size:22px;color:var(--red)}
.pager span.on{background:var(--red);color:#fff}

/* footer */
.site-footer{height:297px;background:var(--footer);color:#fff;text-align:center;padding-top:110px}
.footer-brand{display:flex;align-items:center;justify-content:center;gap:12px}
.footer-brand .brand-mark{width:34px;height:34px;background:#fff}
.footer-brand .brand-name{font-size:40px;color:#fff;font-weight:500}
.footer-nav{display:flex;justify-content:center;gap:32px;font-size:16px;font-weight:500;margin-top:28px}
.footer-rule{width:976px;height:1px;background:#a3242e;margin:22px auto 0}
.copyright{font-size:15px;margin-top:16px;color:#fff}
</style>
</head>
<body>

<header class="site-header">
  <div class="brand"><span class="brand-mark"></span><span class="brand-name">Norvale Talent</span></div>
  <nav class="main-nav"><span>Find Jobs</span><span>Hire Talent</span><span>Explore Consulting Solutions</span><span>Discover Insights</span></nav>
  <div class="header-tools">
    <svg width="16" height="16" viewBox="0 0 16 16"><circle cx="7" cy="7" r="5" fill="none" stroke="#222" stroke-width="2"/><path d="M11 11l4 4" stroke="#222" stroke-width="2"/></svg>
    <span>Sign In</span>
  </div>
</header>

<section class="hero">
  <div class="hero-photo" role="img" aria-label="Photo of a smiling businesswoman in an interview with a colleague in a modern office"></div>
  <div class="hero-content">
    <h1>Your Dream Jobs<br>is Waiting</h1>
    <p>Lorem ipsum dolor sit amet, consectetur adipiscing elit, sed do eiusmod tempor incididunt ut labore et dolore magna aliqua. Quis ipsum suspendisse ultrices gravida.</p>
  </div>
  <div class="search-box">
    <div class="search-labels">
      <div><svg width="18" height="16" viewBox="0 0 18 16"><rect x="1" y="4" width="16" height="11" rx="2" fill="#fff"/><rect x="6" y="1" width="6" height="4" fill="none" stroke="#fff" stroke-width="2"/></svg>Search Job</div>
      <div><svg width="14" height="18" viewBox="0 0 14 18"><path d="M7 0a7 7 0 0 1 7 7c0 5-7 11-7 11S0 12 0 7a7 7 0 0 1 7-7z" fill="#fff"/><circle cx="7" cy="7" r="2.5" fill="#c8202f"/></svg>Location</div>
    </div>
    <div class="search-fields">
      <div class="field">Search Keyword</div>
      <div class="field">Select Location</div>
      <div class="search-btn"><svg width="16" height="16" viewBox="0 0 16 16"><circle cx="7" cy="7" r="5" fill="none" stroke="#fff" stroke-width="2"/><path d="M11 11l4 4" stroke="#fff" stroke-width="2"/></svg></div>
    </div>
  </div>
</section>

<section class="categories">
  <h2 class="section-title">Trending Categories</h2>
  <div class="wrap">
    <div class="cat-row">
      <div class="cat-card"><svg width="140" height="140" viewBox="0 0 140 140"><polygon points="70,4 128,37 128,103 70,136 12,103 12,37" fill="#c8202f"/><rect x="40" y="44" width="60" height="56" rx="6" fill="#fff"/><rect x="52" y="56" width="36" height="26" fill="none" stroke="#222" stroke-width="2"/><path d="M48 90h44" stroke="#222" stroke-width="2"/></svg><h3>Development</h3><small>12k+ Jobs</small></div>
      <div class="cat-card"><svg width="140" height="140" viewBox="0 0 140 140"><polygon points="70,4 128,37 128,103 70,136 12,103 12,37" fill="#c8202f"/><rect x="40" y="44" width="60" height="56" rx="6" fill="#fff"/><path d="M70 92l-18-18a10 10 0 0 1 18-12 10 10 0 0 1 18 12z" fill="none" stroke="#222" stroke-width="2"/><path d="M54 74h8l4-6 4 10 4-4h10" fill="none" stroke="#222" stroke-width="2"/></svg><h3>Health &amp; Care</h3><small>12k+ Jobs</small></div>
      <div class="cat-card"><svg width="140" height="140" viewBox="0 0 140 140"><polygon points="70,4 128,37 128,103 70,136 12,103 12,37" fill="#c8202f"/><rect x="40" y="44" width="60" height="56" rx="6" fill="#fff"/><path d="M52 90V78M60 90V70M68 90V74M76 90V62" stroke="#222" stroke-width="3"/><circle cx="82" cy="80" r="7" fill="none" stroke="#222" stroke-width="2"/></svg><h3>Marketing</h3><small>12k+ Jobs</small></div>
      <div class="cat-card"><svg width="140" height="140" viewBox="0 0 140 140"><polygon points="70,4 128,37 128,103 70,136 12,103 12,37" fill="#c8202f"/><rect x="40" y="44" width="60" height="56" rx="6" fill="#fff"/><circle cx="70" cy="70" r="18" fill="none" stroke="#222" stroke-width="2"/><path d="M62 92h16" stroke="#222" stroke-width="2"/></svg><h3>UI/UX Design</h3><small>12k+ Jobs</small></div>
    </div>
    <div class="dots" style="margin-top:38px"><i></i><i class="on"></i><i></i><i></i></div>
  </div>
</section>

<section class="about">
  <div class="about-text">
    <h2>About Norvale Talent</h2>
    <h4>Explore a faster, easier, and better job search</h4>
    <p>Lorem ipsum dolor sit amet, consectetur adipiscing elit, sed do eiusmod tempor incididunt ut labore et dolore magna aliqua. Quis ipsum sus pendisse ultrices gravida. Risus commodo viverra maecenas acc umsan lacus vel facilisis.</p>
    <ul class="ticks"><li>Sed ut perspiciatis unde omnis iste</li><li>Sed ut perspiciatis unde omnis iste</li><li>Sed ut perspiciatis unde omnis iste</li></ul>
  </div>
  <div class="about-photo" role="img" aria-label="Photo of a candidate shaking hands with a recruiter in an office"></div>
</section>

<section class="how">
  <h2 class="section-title">How It’s Work?</h2>
  <svg class="arrow" style="left:318px;top:178px" width="190" height="40" viewBox="0 0 190 40"><path d="M2 30 Q90 -10 182 28" fill="none" stroke="#222" stroke-width="1.5" stroke-dasharray="5 5"/><path d="M176 20l8 10-12 1" fill="#222"/></svg>
  <svg class="arrow" style="left:698px;top:264px" width="190" height="40" viewBox="0 0 190 40"><path d="M2 8 Q90 50 182 10" fill="none" stroke="#222" stroke-width="1.5" stroke-dasharray="5 5"/><path d="M172 6l12 2-8 10" fill="#222"/></svg>
  <div class="wrap">
    <div class="steps">
      <div class="step"><svg width="140" height="140" viewBox="0 0 140 140"><polygon points="70,4 128,37 128,103 70,136 12,103 12,37" fill="#c8202f"/><rect x="40" y="44" width="60" height="56" rx="6" fill="#fff"/><rect x="56" y="54" width="28" height="36" fill="none" stroke="#222" stroke-width="2"/><path d="M61 64h18M61 72h18M61 80h12" stroke="#222" stroke-width="2"/></svg><br><span class="num">01</span><h3>Create Account</h3><p>Lorem ipsum dolor sit amet, consectetur adipiscing</p></div>
      <div class="step"><svg width="140" height="140" viewBox="0 0 140 140"><polygon points="70,4 128,37 128,103 70,136 12,103 12,37" fill="#c8202f"/><rect x="40" y="44" width="60" height="56" rx="6" fill="#fff"/><circle cx="70" cy="72" r="20" fill="none" stroke="#222" stroke-width="2"/><circle cx="70" cy="66" r="7" fill="none" stroke="#222" stroke-width="2"/><path d="M56 86a16 12 0 0 1 28 0" fill="none" stroke="#222" stroke-width="2"/></svg><br><span class="num">02</span><h3>Complete your profile</h3><p>Lorem ipsum dolor sit amet, consectetur adipiscing</p></div>
      <div class="step"><svg width="140" height="140" viewBox="0 0 140 140"><polygon points="70,4 128,37 128,103 70,136 12,103 12,37" fill="#c8202f"/><rect x="40" y="44" width="60" height="56" rx="6" fill="#fff"/><circle cx="70" cy="64" r="8" fill="none" stroke="#222" stroke-width="2"/><path d="M58 80a12 8 0 0 1 24 0M50 88h40" fill="none" stroke="#222" stroke-width="2"/></svg><br><span class="num">03</span><h3>Apply job or hire</h3><p>Lorem ipsum dolor sit amet, consectetur adipiscing</p></div>
    </div>
  </div>
</section>

<section class="cv-band">
  <div class="cv-photo" role="img" aria-label="Photo of a cheerful woman holding a laptop"></div>
  <div class="cv-text">
    <h3>Get your Matched Jobs in a few minutes.</h3>
    <p>Lorem ipsum dolor sit amet, consectetur adipiscing elit, sed do eiusmod tempor incididunt ut labore et</p>
    <span class="btn"><svg width="16" height="12" viewBox="0 0 16 12"><path d="M4 11a4 4 0 0 1 0-8 5 5 0 0 1 9 1 3.5 3.5 0 0 1 0 7z" fill="#fff"/></svg>Upload Your CV</span>
  </div>
</section>

<section class="testimonials">
  <h2 class="section-title">Testimonials</h2>
  <div class="wrap">
    <div class="quotes">
      <div class="quote"><svg width="62" height="42" viewBox="0 0 62 42"><path d="M2 2h24v22c0 10-6 16-16 18l-2-6c6-2 8-6 8-10H2zM36 2h24v22c0 10-6 16-16 18l-2-6c6-2 8-6 8-10H36z" fill="#c8202f"/></svg><p>Lorem ipsum dolor sit amet, consectetur adipiscing elit, sed do eiusmod tempor incid idunt ut labore et dolore magna aliqua. Quis ipsum suspendisse ultrices gravida.</p><h4>John Peter</h4></div>
      <div class="quote"><svg width="62" height="42" viewBox="0 0 62 42"><path d="M2 2h24v22c0 10-6 16-16 18l-2-6c6-2 8-6 8-10H2zM36 2h24v22c0 10-6 16-16 18l-2-6c6-2 8-6 8-10H36z" fill="#c8202f"/></svg><p>Lorem ipsum dolor sit amet, consectetur adipiscing elit, sed do eiusmod tempor incid idunt ut labore et dolore magna aliqua. Quis ipsum suspendisse ultrices gravida.</p><h4>John Peter</h4></div>
      <div class="quote"><svg width="62" height="42" viewBox="0 0 62 42"><path d="M2 2h24v22c0 10-6 16-16 18l-2-6c6-2 8-6 8-10H2zM36 2h24v22c0 10-6 16-16 18l-2-6c6-2 8-6 8-10H36z" fill="#c8202f"/></svg><p>Lorem ipsum dolor sit amet, consectetur adipiscing elit, sed do eiusmod tempor incid idunt ut labore et dolore magna aliqua. Quis ipsum suspendisse ultrices gravida.</p><h4>John Peter</h4></div>
    </div>
    <div class="dots" style="margin-top:48px"><i></i><i class="on"></i><i></i><i></i></div>
  </div>
</section>

<section class="opps">
  <div class="opps-text">
    <h2>More Opportunities<br>For Everyone</h2>
    <p>Lorem ipsum dolor sit amet, consectetur adipiscing elit, sed do eiusmod tempor incididunt ut labore et dolore magna aliqua. Quis ipsum sus pendisse ultrices gravida. Risus commodo viverra maecenas acc umsan lacus vel facilisis.</p>
    <span class="btn">Learn More</span>
  </div>
  <div class="features">
    <div class="feature"><div class="feature-icon"><svg width="36" height="36" viewBox="0 0 36 36"><rect x="4" y="4" width="20" height="14" fill="none" stroke="#fff" stroke-width="2"/><circle cx="26" cy="24" r="4" fill="none" stroke="#fff" stroke-width="2"/><path d="M18 34a8 6 0 0 1 16 0" fill="none" stroke="#fff" stroke-width="2"/></svg></div><div><h4>Free Coaching</h4><p>Lorem ipsum dolor sit amet, consectetur adipiscing elit, sed do</p></div></div>
    <div class="feature"><div class="feature-icon"><svg width="36" height="36" viewBox="0 0 36 36"><circle cx="18" cy="18" r="14" fill="none" stroke="#fff" stroke-width="2"/><path d="M18 10l2.5 5 5.5.8-4 3.9 1 5.5-5-2.6-5 2.6 1-5.5-4-3.9 5.5-.8z" fill="#fff"/></svg></div><div><h4>Comprehensive Ratings</h4><p>Lorem ipsum dolor sit amet, consectetur adipiscing elit, sed do</p></div></div>
    <div class="feature"><div class="feature-icon"><svg width="36" height="36" viewBox="0 0 36 36"><circle cx="18" cy="10" r="6" fill="none" stroke="#fff" stroke-width="2"/><path d="M6 34V26a12 8 0 0 1 24 0v8z" fill="none" stroke="#fff" stroke-width="2"/></svg></div><div><h4>By Real Employees</h4><p>Lorem ipsum dolor sit amet, consectetur adipiscing elit, sed do</p></div></div>
  </div>
</section>

<section class="insights">
  <h2 class="section-title">Hiring Trends &amp; Insights</h2>
  <div class="post-row">
    <article class="post"><div class="post-img" role="img" aria-label="Photo of a professional handshake across a desk" style="background:linear-gradient(135deg,#8c8784,#e4e0da)"></div><h4>Salary Guide</h4><p>Sed ut perspiciatis unde omnis iste natus error sit voluptatem accusan tium doloremque</p></article>
    <article class="post"><div class="post-img" role="img" aria-label="Photo of a finger pressing a new career start button" style="background:radial-gradient(circle at 55% 55%,#9fb3c4,#2c3540 70%)"></div><h4>Multigenerational Workforce</h4><p>Sed ut perspiciatis unde omnis iste natus error sit voluptatem accusan tium doloremque</p></article>
    <article class="post"><div class="post-img" role="img" aria-label="Photo of job seekers sitting in a row holding job signs" style="background:linear-gradient(180deg,#f2f1ee,#dcd6cc)"></div><h4>What jobs are in demand?</h4><p>Sed ut perspiciatis unde omnis iste natus error sit voluptatem accusan tium doloremque</p></article>
    <article class="post"><div class="post-img" role="img" aria-label="Photo of a laptop showing a job search page" style="background:linear-gradient(135deg,#c9a68a,#f1e6dc)"></div><h4>A Future-Proofed Workforce</h4><p>Sed ut perspiciatis unde omnis iste natus error sit voluptatem accusan tium doloremque</p></article>
  </div>
  <div class="progress"><i></i></div>
  <div class="pager"><span class="on">«</span><span>»</span></div>
</section>

<footer class="site-footer">
  <div class="footer-brand"><span class="brand-mark"></span><span class="brand-name">Norvale Talent</span></div>
  <nav class="footer-nav"><span>Find Jobs</span><span>Hire Talent</span><span>Explore Consulting Solutions</span><span>Discover Insights</span></nav>
  <div class="footer-rule"></div>
  <p class="copyright">Copyright 2024 Norvale Talent. All Rights Reserved.</p>
</footer>

</body>
</html>
```